The most modern business card ever !!!

Our company call “Vendalo”. Vendalo is a technology company specialized in cruises solutions. Out main product is a platform to reserve cruises. This is a revolutionary platform that make easier to travel agencies and final users to reserve cruises across dozen companies like tibba, wernu, hpv, dgb, etc..We are a “start up”, with a young team of developers and we want to transmit it.. For it, we want something different, a modern business card that represent cruises and technology.. When someone receive this card, this person should say: wowww this is different… this is modern… this is a cruise related company..
- diferent, modern
- traditions business card

```html
<!DOCTYPE html>
<html lang="en">
<head>
<meta charset="utf-8">
<title>Vendalo Business Card</title>
<link rel="stylesheet" href="https://fonts.googleapis.com/css2?family=Lato:wght@400;700&display=swap">
<style>
  :root {
    --backdrop: #5b5b5b;
    --card-light: #f3f3f3;
    --card-dark: #050709;
    --card-dark-glow: #14181c;
    --ink: #161616;
    --accent: #1e9fdc;
    --silver: #a6a8aa;
  }
  html, body {
    margin: 0;
    padding: 0;
    width: 1200px;
    height: 900px;
    overflow: hidden;
    background: var(--backdrop);
    font-family: "Lato", sans-serif;
  }
  .canvas {
    position: relative;
    width: 1200px;
    height: 900px;
  }
  .card {
    position: absolute;
    top: 200px;
    width: 310px;
    height: 502px;
    box-sizing: border-box;
  }
  .card-front {
    left: 253px;
    background: var(--card-light);
    border-radius: 76px 0 76px 0;
  }
  .card-back {
    left: 627px;
    background: radial-gradient(ellipse at 50% 50%, var(--card-dark-glow) 0%, var(--card-dark) 65%);
    border-radius: 0 76px 0 76px;
  }
  .brand-name {
    position: absolute;
    margin: 0;
    font-weight: 700;
    letter-spacing: 1px;
    line-height: 1;
    white-space: nowrap;
  }
  .card-front .brand-name {
    left: 42px;
    top: 140px;
    font-size: 52px;
    color: var(--ink);
  }
  .card-back .brand-name {
    left: 0;
    right: 0;
    top: 228px;
    text-align: center;
    font-size: 50px;
    color: var(--silver);
  }
  .contact-block {
    position: absolute;
    left: 32px;
    top: 302px;
    color: var(--ink);
  }
  .person-name {
    margin: 0;
    font-size: 18px;
    font-weight: 700;
    color: var(--accent);
    letter-spacing: 0.2px;
    line-height: 22px;
  }
  .person-role {
    margin: 0 0 6px;
    font-size: 15px;
    line-height: 20px;
  }
  .contact-list {
    list-style: none;
    margin: 0 0 6px;
    padding: 0;
  }
  .contact-list li {
    display: flex;
    align-items: center;
    font-size: 15px;
    line-height: 18.5px;
  }
  .contact-icon {
    width: 13px;
    height: 13px;
    margin-right: 6px;
    fill: var(--accent);
    flex: none;
  }
  .address {
    margin: 0;
    font-size: 15px;
    line-height: 18.5px;
    font-style: normal;
  }
</style>
</head>
<body>
<main class="canvas">
  <section class="card card-front">
    <p class="brand-name">Vendalo</p>
    <div class="contact-block">
      <p class="person-name">MARCUS HALE</p>
      <p class="person-role">Managing Director</p>
      <ul class="contact-list">
        <li>
          <svg class="contact-icon" viewBox="0 0 16 16" aria-hidden="true"><path d="M1 6c0-3 3-4 7-4s7 1 7 4v1h-4V5.5H5V7H1zM4 8h8l2 5v1H2v-1zM8 9.5a2 2 0 1 0 0 4 2 2 0 0 0 0-4z"/></svg>
          055-210 384 667
        </li>
        <li>
          <svg class="contact-icon" viewBox="0 0 16 16" aria-hidden="true"><path d="M4.5 1h7a1 1 0 0 1 1 1v12a1 1 0 0 1-1 1h-7a1 1 0 0 1-1-1V2a1 1 0 0 1 1-1zm.5 2v9h6V3zm3 10a.8.8 0 1 0 0 1.6A.8.8 0 0 0 8 13z"/></svg>
          055-210 384 667
        </li>
        <li>
          <svg class="contact-icon" viewBox="0 0 16 16" aria-hidden="true"><path d="M1 3.5h14v9H1zm1.2 1L8 9l5.8-4.5z"/></svg>
          info@vendalomail.com
        </li>
        <li>
          <svg class="contact-icon" viewBox="0 0 16 16" aria-hidden="true"><circle cx="8" cy="8" r="7"/><path d="M4 5c2 0 2 2 4 2s1 3-1 3-1 3-2 3C3 11 3 8 4 5zm6-2c1 1 3 2 2 4-1 1-2 0-2-1z" fill="#f3f3f3"/></svg>
          www.vendaloweb.com
        </li>
      </ul>
      <address class="address">12345, Address Goes Here<br>Country Name, 123456.</address>
    </div>
  </section>

  <section class="card card-back">
    <p class="brand-name">Vendalo</p>
  </section>
</main>
</body>
</html>
```